Zielgruppe
Ich biete Farbtupferei, Glitzertattoos, Schwangerschaftsbemalung (Belly-Painting), Wunden schminken, Vermietung von einer Popcornmaschine.
Aufgabenstellung
Mein Anliegen betrifft hiermit die Gestaltung einer Website.
In Bezug auf die Website gibt es schon eine gekaufte Domain, welche lautet: frau-pinselmaus.de und kann über VERAX eingerichtet werden.
Auf dieser WEBSITE soll sich folgendes Menü befinden:
- Anfrage stellen/Angebot einholen mit zusätzlicher Frage 'Wie sind Sie auf mich aufmerksam geworden?'
Mit einem Feld für den Namen, E-Mail, Telefonnummer, Gewünschtes Datum.
Sowie die Frage 'Wie sind Sie auf mich aufmerksam geworden?' (zum Ankreuzen) Freunde, Empfehlung, Flyer, soziale medienoder sonstiges.
Gerne auch zum ankreuzen welche Leistung Sie möchten. Farbtupferei, Glitzer Tattoos, Schwangerschaftsbemalung, oder Popcornmaschiene. (So brauchen haben es die Kunden einfacher nur anzukreuzen und ich sehe gleich worum es sich handelt.)
- eine Leistungsübersicht: Farbtupferei, Glitzertattoos, Schwangerschaftsbemalung (Belly-Painting), Wunden schminken, Vermietung von einer Popcornmaschine
- meine Kontaktdaten
- Galerie (es kann eine Auswahl der angehängten Bilder sein)
!!! mein Wunsch wäre, dass sich die Figur von dem Logo in verschiedenen Positionen auf der Website an das Menü angepasst wiederfindet (wenn dies irgendwie machbar ist)
z.B. meine Figur (Logo) stehend am Rand oder liegend.....
- erwünscht ist auch eine Verknüpfung mit einem Findlaeintrag
- Hinweis auf Kontaktor und Lumoravue (bin gerade dabei ein öffentliches Profil dort zu erstellen)
!Wichtig wäre die nötige Einstellung, damit die Website sowohl in der mobilen Version als auch der PC-Version mit ALLEN oben genannten Informationen dargestellt wird!
Dankbar wäre ich noch für die Information, ob für mich laufende Kosten (monatlich oder jährlich) für die Website entstehen?
Mein Logo ist mir sehr wichtig und sollte gut sichtbar und erkennbar sein auch die Schriftart kann auf der Website aufgegriffen werden

```html
<!DOCTYPE html>
<html lang="de">
<head>
<meta charset="utf-8">
<title>Frau Pinselmaus – Farbtupferei &amp; Glitzer Tattoos</title>
<link href="https://fonts.googleapis.com/css2?family=Yanone+Kaffeesatz:wght@400;700&family=Roboto:wght@400;500&family=Roboto+Condensed:wght@400&display=swap" rel="stylesheet">
<style>
  :root{
    --sky:#dff7fd;
    --teal:#1b97ad;
    --slate:#4f555b;
    --ink:#3a3f44;
    --cloud:#ffffff;
    --grass:#6f8a3c;
    --skin:#e3b7a2;
  }
  *{box-sizing:border-box;margin:0;padding:0}
  html,body{width:1200px;height:850px;overflow:hidden;background:#fff}
  body{font-family:"Roboto",sans-serif;color:var(--ink);position:relative}

  .site-header{position:absolute;left:0;top:0;width:1200px;height:100px;background:var(--sky);z-index:3}
  .brand{position:absolute;left:385px;top:26px;display:flex;align-items:center;gap:10px}
  .brand__dot{width:14px;height:14px;border-radius:50%;background:var(--teal)}
  .brand__name{font-family:"Roboto Condensed",sans-serif;font-size:30px;color:var(--teal);letter-spacing:.5px;line-height:1}
  .brand__tag{position:absolute;left:409px;top:62px;font-size:8px;letter-spacing:1.2px;color:var(--slate)}
  .main-nav{position:absolute;left:650px;top:40px;display:flex;gap:22px;align-items:center}
  .main-nav a{font-size:11px;color:var(--slate);text-decoration:none}
  .btn{display:inline-block;font-size:11px;font-weight:500;color:#fff;text-decoration:none;padding:8px 14px;border-radius:1px}
  .btn--teal{background:var(--teal)}
  .btn--slate{background:var(--slate)}
  .main-nav .btn{color:#fff;margin-left:10px}

  .hero{position:absolute;left:0;top:100px;width:1200px;height:480px;
    background:linear-gradient(180deg,#b9b3a9 0%,#9aa35c 35%,var(--grass) 70%,#5d7a33 100%)}
  .hero__legs{position:absolute;left:330px;top:0;width:420px;height:420px;
    background:linear-gradient(90deg,transparent 0%,var(--skin) 20%,#d9a894 50%,var(--skin) 75%,transparent 100%);opacity:.55}
  .hero__title{position:absolute;left:0;width:1200px;top:180px;text-align:center;
    font-family:"Yanone Kaffeesatz",sans-serif;font-weight:700;font-style:italic;font-size:30px;color:#fff;z-index:2}
  .hero__actions{position:absolute;left:0;width:1200px;top:240px;display:flex;justify-content:center;gap:10px;z-index:2}

  .cloud-edge{position:absolute;left:0;width:1200px;z-index:2}
  .cloud-edge--low{z-index:4}

  .about{position:absolute;left:0;top:600px;width:1200px;height:200px;background:var(--sky);z-index:3}
  .about__photo{position:absolute;left:470px;top:14px;width:215px;height:168px;
    background:linear-gradient(135deg,#8a4a24 0%,#b8703e 45%,#3e5a78 100%)}
  .about__text{position:absolute;left:705px;top:14px;width:250px}
  .section-title{font-family:"Yanone Kaffeesatz",sans-serif;font-weight:700;font-size:20px;line-height:1.1;color:var(--teal)}
  .divider{display:flex;align-items:center;gap:4px;margin:4px 0 10px}
  .divider span{height:1px;width:40px;background:var(--teal)}
  .divider i{width:4px;height:4px;border-radius:50%;background:var(--teal)}
  .about__text p{font-size:9px;line-height:1.5;color:var(--slate)}
  .about__text .btn{margin-top:10px;font-size:9px;padding:6px 12px}

  .services-band{position:absolute;left:0;top:820px;width:1200px;height:30px;background:var(--sky);z-index:3}
  .services-head{position:absolute;left:0;width:1200px;top:812px;display:flex;flex-direction:column;align-items:center;z-index:5}
  .services-head .divider{margin:3px 0 0}
</style>
</head>
<body>
  <header class="site-header">
    <div class="brand"><span class="brand__dot"></span><span class="brand__name">Frau Pinselmaus</span></div>
    <div class="brand__tag">FARBTUPFEREI &amp; GLITZER TATTOOS</div>
    <nav class="main-nav">
      <a href="#">Startseite</a>
      <a href="#">Leistungen</a>
      <a href="#">Referenzen</a>
      <a class="btn btn--teal" href="#">Anfrage stellen</a>
    </nav>
  </header>

  <svg class="cloud-edge" style="top:92px;height:16px;z-index:4" viewBox="0 0 1200 16" preserveAspectRatio="none">
    <path d="M0 8 Q300 2 600 9 T1200 6 V0 H0Z" fill="#dff7fd"/>
  </svg>

  <section class="hero">
    <div class="hero__legs" role="img" aria-label="Foto: Kinderbeine mit Glitzer-Tattoos auf einer Wiese"></div>
    <h1 class="hero__title">Farbtupferei &amp; mehr</h1>
    <div class="hero__actions">
      <a class="btn btn--teal" href="#">Leistungen</a>
      <a class="btn btn--slate" href="#">Angebot einholen</a>
    </div>
  </section>

  <svg class="cloud-edge" style="top:450px;height:160px" viewBox="0 0 1200 160" preserveAspectRatio="none">
    <path d="M0 80 Q30 40 70 70 Q100 30 140 65 Q170 45 200 60 Q230 20 280 55 Q320 35 350 50 Q390 10 440 45 Q480 25 510 50 Q550 15 600 45 Q640 25 680 50 Q720 20 760 45 Q800 30 840 55 Q880 20 930 50 Q970 35 1010 55 Q1060 25 1100 55 Q1150 40 1200 60 V160 H0Z" fill="#fff"/>
  </svg>

  <section class="about">
    <svg style="position:absolute;left:0;top:40px" width="560" height="160" viewBox="0 0 560 160">
      <path d="M0 160 V80 Q40 40 90 60 Q120 20 170 45 Q220 30 240 80 Q270 110 300 120 Q340 95 380 120 Q420 110 470 140 L560 160Z" fill="#fff"/>
    </svg>
    <div class="about__photo" role="img" aria-label="Foto: Künstlerin bemalt den Rücken einer Kundin"></div>
    <div class="about__text">
      <h2 class="section-title">Über mich</h2>
      <div class="divider"><span></span><i></i><i></i><i></i></div>
      <p>Frau Pinselmaus steht für kleine Abenteuer und Spaß, während Kinder in eine Welt voller Farben und magischem Glanz eintauchen. Mein vielfältiges Angebot verwandelt Ihr Fest in ein Lieblingserlebnis mit bunten Motiven und glitzernden Entdeckungen. Erleben Sie unvergessliche Momente mit mir.</p>
      <a class="btn btn--teal" href="#">Kontakt</a>
    </div>
  </section>

  <svg class="cloud-edge cloud-edge--low" style="top:792px;height:30px" viewBox="0 0 1200 30" preserveAspectRatio="none">
    <path d="M0 20 Q300 10 600 16 T1200 12 V30 H0Z" fill="#dff7fd"/>
    <path d="M0 0 H1200 V12 Q900 22 600 16 T0 20Z" fill="#fff"/>
  </svg>
  <div class="services-band"></div>

  <div class="services-head">
    <h2 class="section-title">Meine Leistungen</h2>
    <div class="divider"><span></span><i></i><i></i><i></i><span></span></div>
  </div>
</body>
</html>
```